Accountability Project Graphics

I want to create 10 social media graphics (new Instagram size 4:5 (1080 x 1350 pixels) focusing on our Quilvo Accountability App, using any of the 3 pictures attached. Use the attached pics only, NO RANDOM STOCK PHOTOGRAPHY. For the color scheme, use the landing page colors/fonts (attached).
You can add any of the 3 photos attached but I mainly need BOLD text that includes these headlines and sub-headlines on them.
Please NOTE for all the headlines below, also add this sub-headline on each graphic:
Stay Consistent with RT in Your Pocket!
Here are the headlines:
• Stop Starting Over Every Monday
• You don't need more willpower. You need more support
• Built for women who are tired of doing this alone
• When Motivation Fades, RT Checks In
• The Support System You've Been Missing
• Support When Motivation Disappears
• What if RT Checked in Every Day?
• The Missing Piece Isn't Another Diet
• Eat the food you love. Stay accountable every day.
• One Bad Meal Doesn't Mean You Failed
women over 40 trying to lose weight

```html
<!DOCTYPE html>
<html lang="en">
<head>
<meta charset="utf-8">
<title>Accountability App Social Graphics</title>
<link rel="stylesheet" href="https://fonts.googleapis.com/css2?family=Gelasio:ital,wght@0,700;1,700&family=Montserrat:wght@600;700&display=swap">
<style>
  :root {
    --board: #4a4a4a;
    --blush: #fbebed;
    --plum: #2d1d3d;
    --rose: #c9537a;
    --hot-pink: #d94073;
    --white: #ffffff;
    --serif: "Gelasio", Georgia, serif;
    --sans: "Montserrat", Arial, sans-serif;
  }
  * { margin: 0; padding: 0; box-sizing: border-box; }
  html, body { width: 1022px; height: 1200px; overflow: hidden; }
  body { background: var(--board); position: relative; font-family: var(--sans); }

  .post { position: absolute; width: 431px; height: 539px; overflow: hidden; }
  .post--monday { left: 48px; top: 45px; background: var(--blush); }
  .post--willpower { left: 535px; top: 45px; background: var(--blush); }
  .post--motivation { left: 48px; top: 623px; background: var(--plum); }
  .post--women { left: 534px; top: 623px; background: linear-gradient(180deg, #2f1e3c 0%, #6b2a55 35%, #b13f6d 70%, #d94a79 100%); }

  .headline { position: absolute; font-family: var(--serif); font-weight: 700; line-height: 1; }
  .headline .line { display: block; }
  .accent { color: var(--rose); }
  .accent--italic { font-style: italic; }
  .tagline { position: absolute; font-family: var(--sans); font-weight: 600; letter-spacing: 0.3px; }

  /* Post 1 */
  .highlight-band { position: absolute; left: 0; top: 35px; width: 382px; height: 60px; background: var(--white); border-radius: 0 16px 4px 0; box-shadow: 18px 0 24px rgba(255,255,255,0.6); }
  .post--monday .headline { left: 22px; top: 40px; font-size: 52px; color: var(--plum); line-height: 56px; }
  .post--monday .tagline { left: 22px; top: 226px; font-size: 16.5px; color: #1c1420; }
  .post--monday .photo { position: absolute; left: 6px; top: 262px; width: 370px; height: 277px;
    background: radial-gradient(ellipse at 55% 55%, #b0466f 0%, #6e4a82 30%, rgba(220,190,200,0.6) 62%, rgba(251,235,237,0) 80%); }

  /* Post 2 */
  .post--willpower .photo { position: absolute; left: 270px; top: 0; width: 161px; height: 539px;
    background: linear-gradient(180deg, rgba(251,235,237,0) 0%, #2a2b3e 12%, #1f2336 60%, #1b2033 100%);
    border-radius: 60px 0 0 0; }
  .post--willpower .headline { left: 22px; top: 20px; font-size: 50px; line-height: 62px; color: var(--plum); }
  .post--willpower .tagline { left: 22px; top: 468px; font-size: 17px; line-height: 29px; color: #1c1420; }

  /* Post 3 */
  .post--motivation .headline { left: 23px; top: 30px; font-size: 41px; line-height: 54px; color: var(--white); }
  .post--motivation .accent { color: var(--hot-pink); }
  .post--motivation .tagline { left: 22px; top: 192px; font-size: 17px; color: var(--white); }
  .post--motivation .photo { position: absolute; left: 73px; top: 225px; width: 310px; height: 226px;
    background: linear-gradient(180deg, #5a3a3a 0%, #34486e 45%, #2e3f63 100%); border-radius: 90px 90px 0 0; }
  .post--motivation .base-band { position: absolute; left: 0; top: 440px; width: 431px; height: 99px; }

  /* Post 4 */
  .post--women .headline { left: 0; top: 28px; width: 431px; text-align: center; font-size: 64px; line-height: 68px; color: var(--white); }
  .post--women .accent { color: var(--hot-pink); }
  .post--women .tagline { left: 0; top: 462px; width: 431px; text-align: center; font-size: 17px; line-height: 29px; color: var(--white); }
</style>
</head>
<body>

  <section class="post post--monday">
    <div class="highlight-band"></div>
    <h2 class="headline">
      <span class="line">Stop Starting</span>
      <span class="line">Over <span class="accent">Every</span></span>
      <span class="line accent accent--italic">Monday</span>
    </h2>
    <p class="tagline">Stay Consistent with RT in Your Pocket!</p>
    <div class="photo" role="img" aria-label="Photo of two women embracing and laughing in a store"></div>
  </section>

  <section class="post post--willpower">
    <div class="photo" role="img" aria-label="Photo of a smiling woman in a dark lace outfit standing with hand on hip"></div>
    <h2 class="headline">
      <span class="line">You don't</span>
      <span class="line">need</span>
      <span class="line">more will</span>
      <span class="line accent accent--italic">POWER.</span>
      <span class="line">You need</span>
      <span class="line">more</span>
      <span class="line">support</span>
    </h2>
    <p class="tagline">Stay Consistent with RT in<br>Your Pocket!</p>
  </section>

  <section class="post post--motivation">
    <h2 class="headline">
      <span class="line">When Motivation</span>
      <span class="line">Fades, <span class="accent accent--italic">RT Checks</span></span>
      <span class="line accent accent--italic">In</span>
    </h2>
    <p class="tagline">Stay Consistent with RT in Your Pocket!</p>
    <div class="photo" role="img" aria-label="Photo of two women in denim laughing together"></div>
    <svg class="base-band" viewBox="0 0 431 99" preserveAspectRatio="none" aria-hidden="true">
      <path d="M0 0 Q215 6 431 6 L431 99 L0 99 Z" fill="var(--hot-pink)"/>
    </svg>
  </section>

  <section class="post post--women">
    <h2 class="headline">
      <span class="line">Built for</span>
      <span class="line accent">WOMEN</span>
      <span class="line">who are</span>
      <span class="line">tired of</span>
      <span class="line">doing this</span>
      <span class="line">alone</span>
    </h2>
    <p class="tagline">Stay Consistent with RT in<br>Your Pocket!</p>
  </section>

</body>
</html>
```